Business Card Design

New business card design

Target Market(s)

Residential & Commercial Property Managers

Industry/Entity Type

Plumbing Services

Contact Information for Business Card

Name - Rowan Keddle, title - Director, Phone Number - 0431 286 517, email - rowan@tbk-plumbing.com.au, Company ABN - 73 215 904 386,

Font styles to use
Sans Serif

Colors
0054AA
0677BA
7BADD7
CADEEF
E8F1F8

```html
<!DOCTYPE html>
<html lang="en">
<head>
<meta charset="utf-8">
<title>TBK Plumbing Services – Business Card</title>
<link href="https://fonts.googleapis.com/css2?family=Arimo:wght@400;700&display=swap" rel="stylesheet">
<style>
  :root {
    --stage: #3a3b3d;
    --card-dark: #1d2228;
    --card-dark-2: #2a323b;
    --card-blue: #03adef;
    --ink-dark: #12181f;
    --ink-light: #ffffff;
    --accent-drop: #0aa6e8;
  }
  html, body {
    margin: 0;
    padding: 0;
    width: 1200px;
    height: 689px;
    overflow: hidden;
    background: var(--stage);
    font-family: "Arimo", Arial, sans-serif;
  }
  .canvas {
    position: relative;
    width: 1200px;
    height: 689px;
  }
  .card {
    position: absolute;
    top: 186px;
    width: 520px;
    height: 317px;
    border-radius: 18px;
    overflow: hidden;
    box-shadow: 0 12px 30px rgba(0,0,0,0.35);
  }
  .card-front { left: 50px; background: var(--card-dark); }
  .card-back  { left: 630px; background: var(--card-blue); }

  .droplet-pattern {
    position: absolute;
    inset: 0;
    background: radial-gradient(ellipse at 70% 30%, var(--card-dark-2), var(--card-dark) 70%);
  }
  .brand {
    position: absolute;
    left: 0; right: 0;
    top: 96px;
    text-align: center;
    color: var(--ink-light);
  }
  .brand-name {
    display: inline-flex;
    align-items: center;
    gap: 14px;
    font-size: 82px;
    font-weight: 400;
    line-height: 1;
    letter-spacing: 2px;
  }
  .brand-dot {
    width: 18px;
    height: 18px;
    border-radius: 50%;
    background: var(--accent-drop);
  }
  .brand-tagline {
    margin-top: 22px;
    font-size: 13px;
    letter-spacing: 9px;
    text-transform: lowercase;
  }

  .contact-block {
    position: absolute;
    left: 0; right: 0;
    top: 0; bottom: 0;
    display: flex;
    align-items: center;
    justify-content: center;
    gap: 18px;
  }
  .identity { text-align: right; }
  .person-name {
    font-size: 27px;
    font-weight: 700;
    color: var(--ink-dark);
    line-height: 1.1;
  }
  .person-title {
    font-size: 15px;
    color: var(--ink-light);
    margin-top: 4px;
  }
  .divider {
    width: 1px;
    height: 70px;
    background: var(--ink-light);
  }
  .details {
    list-style: none;
    margin: 0;
    padding: 0;
    color: var(--ink-light);
    font-size: 15px;
    line-height: 1.45;
  }
  .details li { display: flex; align-items: center; gap: 7px; }
  .details svg { width: 12px; height: 12px; fill: var(--ink-dark); }
</style>
</head>
<body>
<main class="canvas">
  <section class="card card-front">
    <div class="droplet-pattern" role="img" aria-label="Pattern of raised dark water droplets across the card"></div>
    <div class="brand">
      <div class="brand-name">tbk<span class="brand-dot"></span></div>
      <div class="brand-tagline">plumbing services</div>
    </div>
  </section>

  <section class="card card-back">
    <div class="contact-block">
      <div class="identity">
        <div class="person-name">Rowan Keddle</div>
        <div class="person-title">Director</div>
      </div>
      <div class="divider"></div>
      <ul class="details">
        <li>ABN - 73 215 904 386</li>
        <li>
          <svg viewBox="0 0 24 24" aria-hidden="true"><path d="M6.6 10.8a15.1 15.1 0 0 0 6.6 6.6l2.2-2.2a1 1 0 0 1 1-.25 11.4 11.4 0 0 0 3.6.57 1 1 0 0 1 1 1V20a1 1 0 0 1-1 1A17 17 0 0 1 3 4a1 1 0 0 1 1-1h3.5a1 1 0 0 1 1 1c0 1.25.2 2.45.57 3.57a1 1 0 0 1-.25 1z"/></svg>
          0431 286 517
        </li>
        <li>
          <svg viewBox="0 0 24 24" aria-hidden="true"><path d="M2 5h20v14H2z M3 6l9 7 9-7" fill="var(--ink-dark)"/><path d="M3 6l9 7 9-7" fill="none" stroke="#03adef" stroke-width="1.6"/></svg>
          rowan@tbk-plumbing.com.au
        </li>
      </ul>
    </div>
  </section>
</main>
</body>
</html>
```